Dermatology at Your Door Logo and business card

We provide dermatological services to the community. This includes Assisted Living Facilities, nursing homes and to large cooperation, Health fairs etc. We provide a health care provider that travels to institutions, providing these services. All procedures and surgeries are done onsite in one of our state of the art mobile clinics. We provide services including, but not limited to; skin biopsies, skin surgeries , surgical procedures including skin cancer removal mole removal and treatment of various skin disorders. we bring mobile Dermatology to you.

Industry/Entity Type

Business

Contact Information for Business Card

Need Logo address phone number, email website

Logo Text

Dermatology at Your Door

Logo styles of interest
Emblem Logo
Abstract Logo
Character Logo
Lettermark Logo
Requirements
Must have
• Marcus Tilden ARNP DN-C
• Medical Facilitator
• P. (407) 555-3914
• Fax (386) 555-7281

```html
<!DOCTYPE html>
<html lang="en">
<head>
<meta charset="utf-8">
<title>Dermatology at Your Door – May Appointment Card</title>
<link rel="stylesheet" href="https://fonts.googleapis.com/css2?family=Questrial&family=Mulish:wght@400;500&display=swap">
<style>
  :root {
    --teal-deep: #0d6464;
    --teal-text: #0f6262;
    --orange: #f7a21b;
    --mint: #e0f1f1;
    --white: #ffffff;
    --paper: #ffffff;
  }
  html, body {
    margin: 0;
    padding: 0;
    width: 1200px;
    height: 703px;
    overflow: hidden;
    background: var(--paper);
  }
  .canvas {
    position: relative;
    width: 1200px;
    height: 703px;
  }
  .card {
    position: absolute;
    left: 24px;
    top: 19px;
    width: 1152px;
    height: 663px;
    background: var(--mint);
  }
  .card__header {
    position: absolute;
    left: 0;
    top: 0;
    width: 100%;
    height: 217px;
    background: var(--teal-deep);
  }
  .card__stripe {
    position: absolute;
    left: 0;
    width: 100%;
    height: 10px;
    background: var(--orange);
  }
  .card__stripe--top { top: 217px; }
  .card__stripe--bottom { top: 603px; }
  .card__footer {
    position: absolute;
    left: 0;
    top: 613px;
    width: 100%;
    height: 50px;
    background: var(--teal-deep);
    display: flex;
    flex-direction: column;
    align-items: center;
    justify-content: center;
    font-family: "Mulish", sans-serif;
    font-size: 13px;
    line-height: 18px;
    color: var(--white);
    letter-spacing: 0.3px;
    white-space: nowrap;
  }
  .contact__name { font-weight: 500; }
  .contact__sep { color: var(--orange); padding: 0 8px; }
  .brand {
    position: absolute;
    left: 0;
    top: 0;
    width: 100%;
    height: 217px;
    display: flex;
    align-items: center;
    justify-content: center;
    gap: 18px;
  }
  .brand__dot {
    width: 64px;
    height: 64px;
    border-radius: 50%;
    background: var(--orange);
    flex: none;
  }
  .brand__name {
    font-family: "Questrial", sans-serif;
    font-size: 46px;
    color: var(--white);
    letter-spacing: 0.5px;
    white-space: nowrap;
  }
  .title {
    position: absolute;
    left: 0;
    top: 249px;
    width: 100%;
    margin: 0;
    text-align: center;
    font-family: "Mulish", sans-serif;
    font-weight: 500;
    font-size: 38px;
    letter-spacing: 3px;
    color: var(--teal-text);
  }
  .slot {
    position: absolute;
    display: flex;
    align-items: flex-end;
    width: 408px;
  }
  .slot__number {
    font-family: "Mulish", sans-serif;
    font-size: 21px;
    color: var(--teal-text);
    width: 35px;
    line-height: 1;
  }
  .slot__line {
    flex: 1;
    border-bottom: 2px solid var(--teal-text);
    margin-bottom: 3px;
  }
  .slot--left { left: 80px; }
  .slot--right { left: 655px; }
  .row-1 { top: 356px; }
  .row-2 { top: 450px; }
  .row-3 { top: 543px; }
</style>
</head>
<body>
<div class="canvas">
  <div class="card">
    <header class="card__header">
      <div class="brand">
        <span class="brand__dot"></span>
        <span class="brand__name">Dermatology at Your Door</span>
      </div>
    </header>
    <div class="card__stripe card__stripe--top"></div>

    <h1 class="title">May Appointment</h1>

    <div class="slot slot--left row-1"><span class="slot__number">01</span><span class="slot__line"></span></div>
    <div class="slot slot--left row-2"><span class="slot__number">02</span><span class="slot__line"></span></div>
    <div class="slot slot--left row-3"><span class="slot__number">03</span><span class="slot__line"></span></div>
    <div class="slot slot--right row-1"><span class="slot__number">04</span><span class="slot__line"></span></div>
    <div class="slot slot--right row-2"><span class="slot__number">05</span><span class="slot__line"></span></div>
    <div class="slot slot--right row-3"><span class="slot__number">06</span><span class="slot__line"></span></div>

    <div class="card__stripe card__stripe--bottom"></div>
    <footer class="card__footer contact">
      <div class="contact__line">
        <span class="contact__name">Marcus Tilden ARNP DN-C</span><span class="contact__sep">|</span>Medical Facilitator<span class="contact__sep">|</span>P. (407) 555-3914<span class="contact__sep">|</span>Fax (386) 555-7281
      </div>
      <div class="contact__line">
        1420 Harbor Lane, Orlando, FL 32801<span class="contact__sep">|</span>care@dermatyourdoor.com<span class="contact__sep">|</span>www.dermatyourdoor.com
      </div>
    </footer>
  </div>
</div>
</body>
</html>
```